Business card design for Brivo Engineering Tandem

We need a new business card design along with all the necessary to place an order. The company is Brivo Engineering Tandem and we recently updated our logo.

```html
<!DOCTYPE html>
<html lang="en">
<head>
<meta charset="utf-8">
<title>Brivo Engineering Tandem – Business Card</title>
<link rel="stylesheet" href="https://fonts.googleapis.com/css2?family=Montserrat:wght@400;500;600;700&display=swap">
<style>
  :root {
    --stage: #3b3b3d;
    --card-white: #f1f1f0;
    --gold: #d7b21a;
    --gold-deep: #c29f12;
    --ink: #2a2a2a;
    --grey: #7a7a7a;
  }
  * { margin: 0; padding: 0; box-sizing: border-box; }
  html, body {
    width: 1200px; height: 1059px; overflow: hidden;
    background: var(--stage);
    font-family: "Montserrat", sans-serif;
  }
  .canvas { position: relative; width: 1200px; height: 1059px; }
  .card {
    position: absolute;
    border-radius: 24px;
    overflow: hidden;
  }
  .card-front {
    left: 256px; top: 100px; width: 688px; height: 393px;
    background: var(--card-white);
  }
  .card-back {
    left: 253px; top: 536px; width: 694px; height: 396px;
    background: var(--gold);
  }
  .brand {
    position: absolute; left: 60px; top: 174px; width: 286px;
    display: flex; align-items: center; gap: 12px;
  }
  .brand-mark { width: 22px; height: 22px; background: var(--gold); flex: none; }
  .brand-name {
    color: var(--grey); font-weight: 600; font-size: 16px;
    line-height: 1.2; letter-spacing: 1px; text-transform: uppercase;
    white-space: nowrap;
  }
  .divider {
    position: absolute; left: 366px; top: 90px;
    width: 2px; height: 213px; background: var(--gold);
  }
  .details { position: absolute; left: 394px; top: 88px; color: var(--ink); }
  .person-name {
    color: var(--gold); font-weight: 700; font-size: 27px;
    letter-spacing: 0.5px; line-height: 1.1; text-transform: uppercase;
    white-space: nowrap;
  }
  .person-role { font-size: 18px; font-weight: 500; margin-top: 4px; }
  .address { font-size: 18px; font-weight: 500; line-height: 28px; margin-top: 16px; }
  .contacts { list-style: none; margin-top: 12px; }
  .contacts li {
    display: flex; align-items: center; gap: 9px;
    font-size: 18px; font-weight: 500; line-height: 27px;
    white-space: nowrap;
  }
  .contacts svg { width: 15px; height: 15px; fill: var(--gold); flex: none; }
  .back-brand {
    position: absolute; inset: 0;
    display: flex; align-items: center; justify-content: center; gap: 22px;
  }
  .back-brand .brand-mark { width: 44px; height: 44px; background: var(--gold-deep); }
  .back-brand .brand-name {
    color: var(--gold-deep); font-size: 40px; letter-spacing: 3px; line-height: 1.1;
  }
</style>
</head>
<body>
<main class="canvas">
  <section class="card card-front">
    <div class="brand">
      <span class="brand-mark"></span>
      <span class="brand-name">Brivo<br>Engineering Tandem</span>
    </div>
    <div class="divider"></div>
    <div class="details">
      <h1 class="person-name">Marcus Delane</h1>
      <p class="person-role">Managing Director</p>
      <p class="address">Your address, City<br>State, Zip 1234</p>
      <ul class="contacts">
        <li>
          <svg viewBox="0 0 16 16"><path d="M2 7c0-3 3-4 6-4s6 1 6 4h-3l-.5-1.5h-5L5 7zM4 8h8l1 5H3z"/></svg>
          123 456 789
        </li>
        <li>
          <svg viewBox="0 0 16 16"><path d="M1 4h14v1L8 9 1 5zM1 6.5l7 4 7-4V12H1z"/></svg>
          info@yourmail.com
        </li>
        <li>
          <svg viewBox="0 0 16 16"><circle cx="8" cy="8" r="7"/></svg>
          www.yourwebsite.com
        </li>
      </ul>
    </div>
  </section>

  <section class="card card-back">
    <div class="back-brand">
      <span class="brand-mark"></span>
      <span class="brand-name">Brivo<br>Engineering Tandem</span>
    </div>
  </section>
</main>
</body>
</html>
```